Veltra Metrics New Website for Health Benefits Plan Decisioneering Tool Launch

Veltra Metrics is a SaaS provider of health benefits comparison tools. We need a new simple SaaS focused website to direct customers to our product

Target Market(s)

General Public comparing their health benefits plans from their employer or from the state exchanges in the US

Coding

Coded - Design and coding required

Number of Pages Required

3 page

Requirements
Must have
• Main page - "Know the Best Health Benefits Plan for You!"
Graphic of a person looking over papers on their desk
Compare Now button to link to SaaS product
About Us
Product Page

https://plimbo.example/top-app-pages/

```html
<!DOCTYPE html>
<html lang="en">
<head>
<meta charset="utf-8">
<title>Veltra Metrics – Know the Best Health Benefits Plan for You</title>
<link href="https://fonts.googleapis.com/css2?family=Poppins:wght@600;700&family=Roboto:wght@300;400;500&display=swap" rel="stylesheet">
<style>
:root{
  --blue:#2c8fd6;
  --blue-soft:#5db3e4;
  --ink:#1f1f1f;
  --text:#5f5f5f;
  --muted:#8a8a8a;
  --line:#e4e4e4;
  --card:#d4eefb;
  --grey-band:#efefef;
  --footer:#1b1b1b;
  --white:#ffffff;
}
*{box-sizing:border-box;margin:0;padding:0}
html,body{width:1200px;height:3372px;overflow:hidden}
body{position:relative;background:var(--white);font-family:"Roboto",sans-serif;color:var(--text)}
.abs{position:absolute}
h2.section-title{position:absolute;left:0;width:1200px;text-align:center;font-family:"Poppins",sans-serif;font-weight:700;font-size:31px;color:var(--ink);letter-spacing:-.5px}
.divider{position:absolute;left:50%;transform:translateX(-50%);display:flex;align-items:center;gap:10px}
.divider span{display:block;height:1px;background:var(--blue);width:66px}
.divider i{display:block;width:12px;height:12px;border-radius:50%;background:var(--blue)}
.lead{position:absolute;text-align:center;font-size:14.5px;line-height:23px;font-weight:300;color:var(--text)}

/* header */
.site-header{position:absolute;top:0;left:0;width:1200px;height:65px;background:var(--white)}
.brand{position:absolute;left:111px;top:20px;font-size:22px;font-weight:400;color:var(--blue);letter-spacing:.5px}
.nav{position:absolute;left:403px;top:25px;display:flex;gap:26px;font-size:14.5px;color:#3b3b3b}
.nav a{color:inherit;text-decoration:none}
.nav a.active{color:var(--blue)}
.sign-in{position:absolute;left:987px;top:13px;width:99px;height:43px;border:2px solid var(--blue);border-radius:5px;color:var(--blue);font-size:14.5px;display:flex;align-items:center;justify-content:center}

/* hero */
.hero{position:absolute;top:65px;left:0;width:1200px;height:558px;background:linear-gradient(115deg,#8a9ab4 0%,#5d6f8f 45%,#2f3e5c 100%)}
.hero h1{position:absolute;top:155px;left:0;width:1200px;text-align:center;font-family:"Poppins",sans-serif;font-weight:700;font-size:40px;line-height:47px;color:var(--white);letter-spacing:-1px}
.btn-compare{position:absolute;left:524px;top:286px;width:153px;height:43px;background:var(--blue);border-radius:3px;color:var(--white);font-size:14.5px;font-weight:500;display:flex;align-items:center;justify-content:center}

/* services */
.photo-desk{left:111px;top:904px;width:423px;height:552px;border-radius:6px;background:linear-gradient(160deg,#e9ddd4 0%,#b8a497 45%,#284f86 75%,#1f3a66 100%)}
.service{position:absolute;width:240px;text-align:center}
.service .icon{width:102px;height:102px;margin:0 auto;border:1.5px solid var(--blue);border-radius:50%;display:flex;align-items:center;justify-content:center}
.service h3{margin-top:23px;font-family:"Poppins",sans-serif;font-weight:600;font-size:17px;color:var(--ink)}
.service p{margin-top:14px;font-size:14px;line-height:22px;font-weight:300;color:var(--text)}
.service .more{margin-top:14px;font-size:14px;color:var(--blue);display:flex;justify-content:center;align-items:center;gap:8px}

/* about */
.about-band{left:0;top:1554px;width:600px;height:432px;background:linear-gradient(120deg,#56a9df,#6bbde9)}
.about-photo{left:600px;top:1554px;width:600px;height:432px;background:linear-gradient(135deg,#c9d2db 0%,#7d8c99 40%,#2e3640 100%)}
.about-band h2{position:absolute;left:91px;top:86px;font-family:"Poppins",sans-serif;font-weight:700;font-size:31px;color:var(--white)}
.about-band .divider{left:91px;top:138px;transform:none}
.about-band .divider span{background:var(--white);width:58px}
.about-band .divider i{background:var(--white)}
.about-band p{position:absolute;left:91px;top:177px;width:410px;font-size:14.5px;line-height:23px;font-weight:300;color:var(--white)}
.btn-outline{position:absolute;left:91px;top:296px;width:115px;height:43px;border:2px solid var(--white);border-radius:5px;color:var(--white);font-size:14.5px;display:flex;align-items:center;justify-content:center}

/* benefits */
.photo-handshake{left:111px;top:2251px;width:479px;height:307px;background:linear-gradient(90deg,#e4ebf1 0%,#c9d3dd 50%,#3a4050 100%)}
.timeline{left:651px;top:2274px;width:2px;height:290px;background:var(--blue-soft)}
.benefit{position:absolute;left:626px;width:460px}
.benefit .dot{position:absolute;left:0;top:0;width:52px;height:52px;border-radius:50%;background:#cbe7f7;display:flex;align-items:center;justify-content:center}
.benefit .dot b{width:36px;height:36px;border-radius:50%;background:var(--blue-soft);border:2px solid var(--white);display:flex;align-items:center;justify-content:center}
.benefit h3{position:absolute;left:74px;top:-2px;font-family:"Poppins",sans-serif;font-weight:600;font-size:17px;color:var(--ink)}
.benefit p{position:absolute;left:75px;top:30px;width:385px;font-size:12.5px;line-height:19.5px;font-weight:300;color:var(--text)}

/* testimonials */
.testi-band{left:0;top:2653px;width:1200px;height:389px;background:linear-gradient(135deg,#f3f3f3,#e6e6e6)}
.testi{position:absolute;top:2810px;width:480px;height:139px;background:var(--card);border-radius:4px}
.testi .avatar{position:absolute;left:28px;top:26px;width:50px;height:50px;border-radius:50%;background:linear-gradient(135deg,#b08a70,#4a3a30)}
.testi p{position:absolute;left:104px;top:24px;width:340px;font-size:14px;line-height:20px;font-weight:300;color:#4a4a4a}
.testi .who{position:absolute;left:270px;top:86px;font-size:14px;line-height:21px;font-weight:500;color:#2a2a2a;text-align:left}
.testi .who small{display:block;font-size:14px;color:#555;padding-left:8px;font-weight:500}
.dots{left:578px;top:2988px;display:flex;gap:4px}
.dots i{display:block;width:8px;height:8px;border-radius:50%;background:#555}
.dots i:first-child{background:var(--blue)}

/* footer */
.site-footer{position:absolute;left:0;top:3042px;width:1200px;height:330px;background:var(--footer);color:#f0f0f0}
.site-footer .brand{left:111px;top:78px}
.f-about{position:absolute;left:111px;top:128px;width:190px;font-size:14px;line-height:21.5px;color:#e8e8e8}
.f-head{position:absolute;top:70px;font-family:"Roboto",sans-serif;font-weight:500;font-size:16px;letter-spacing:.3px;color:var(--white)}
.f-links{position:absolute;left:381px;top:122px;font-size:14px;line-height:23.3px;color:#e8e8e8;list-style:none}
.f-contact{position:absolute;left:560px;top:122px;font-size:14px;line-height:20px;color:#e8e8e8}
.f-contact div{display:flex;gap:10px;align-items:flex-start;margin-bottom:19px}
.newsletter{position:absolute;left:826px;top:119px;width:264px;height:48px;border:1.5px solid var(--white);display:flex;align-items:center;justify-content:space-between;padding:0 16px;font-size:11px;color:#ddd}
.social{position:absolute;left:825px;top:184px;display:flex;gap:4px}
.social i{display:block;width:17px;height:17px;border-radius:50%;background:var(--white)}
.f-rule{position:absolute;left:111px;top:274px;width:979px;height:1px;background:#3a3a3a}
.copyright{position:absolute;left:0;top:292px;width:1200px;text-align:center;font-size:14px;color:#e8e8e8}
</style>
</head>
<body>

<header class="site-header">
  <div class="brand">VELTRA METRICS</div>
  <nav class="nav">
    <a class="active">HOME</a><a>ABOUT US</a><a>SERVICES</a><a>BENEFITS</a><a>TESTIMONIALS</a><a>CONTACT US</a>
  </nav>
  <a class="sign-in">SIGN IN</a>
</header>

<section class="hero" role="img" aria-label="Photo of a person at a desk with a laptop, reviewing papers with a pen">
  <h1>KNOW THE BEST HEALTH BENEFITS<br>PLAN FOR YOU!</h1>
  <a class="btn-compare">COMPARE NOW</a>
</section>

<h2 class="section-title" style="top:685px">WHAT WE DO</h2>
<div class="divider" style="top:740px"><span></span><i></i><span></span></div>
<p class="lead" style="left:155px;top:789px;width:890px">Lorem ipsum dolor sit amet, consectetur adipiscing elit, sed do eiusmod tempor incididunt ut labore et dolore magna aliqua. Ut enim ad minim veniam, quis nostrud exercitation ullamco laboris nisi ut aliquip ex ea commodo consequat. Duis aute irure dolor in reprehenderit in voluptate velit esse cillum dolore eu fugiat nulla pariatur. Excepteur sint occaecat cupidatat non proident.</p>

<div class="abs photo-desk" role="img" aria-label="Photo of a businessman in a blue suit writing notes beside a laptop"></div>

<div class="service" style="left:566px;top:904px">
  <div class="icon"><svg width="50" height="50" viewBox="0 0 50 50" fill="none" stroke="#2c8fd6" stroke-width="1.6"><path d="M14 22a8 8 0 0 1 15-4 6 6 0 0 1 9 5h-24z"/><rect x="10" y="26" width="24" height="14" rx="1"/><path d="M6 43h32"/><rect x="37" y="30" width="7" height="12" rx="1"/></svg></div>
  <h3>Lorem ipsum</h3>
  <p>Duis aute irure dolor in reprehenderit in voluptate velit esse cillum dolore eu fugiat nulla pariatur.</p>
  <div class="more">Read More <svg width="16" height="8" viewBox="0 0 16 8"><path d="M0 4h13M10 1l4 3-4 3" stroke="#2c8fd6" stroke-width="2" fill="none"/></svg></div>
</div>
<div class="service" style="left:853px;top:904px">
  <div class="icon"><svg width="50" height="50" viewBox="0 0 50 50" fill="none" stroke="#2c8fd6" stroke-width="1.6"><rect x="9" y="14" width="32" height="20" rx="1"/><path d="M20 40h10M25 34v6"/><rect x="18" y="8" width="12" height="16"/><path d="M22 14h4M24 12v4"/></svg></div>
  <h3>Lorem ipsum</h3>
  <p>Duis aute irure dolor in reprehenderit in voluptate velit esse cillum dolore eu fugiat nulla pariatur.</p>
  <div class="more">Read More <svg width="16" height="8" viewBox="0 0 16 8"><path d="M0 4h13M10 1l4 3-4 3" stroke="#2c8fd6" stroke-width="2" fill="none"/></svg></div>
</div>
<div class="service" style="left:566px;top:1204px">
  <div class="icon"><svg width="50" height="50" viewBox="0 0 50 50" fill="none" stroke="#2c8fd6" stroke-width="1.6"><circle cx="25" cy="24" r="9"/><path d="M25 19v10M20 24h10"/><path d="M10 30c4 6 10 9 17 8M40 18c-4-6-10-9-17-8"/></svg></div>
  <h3>Lorem ipsum</h3>
  <p>Duis aute irure dolor in reprehenderit in voluptate velit esse cillum dolore eu fugiat nulla pariatur.</p>
  <div class="more">Read More <svg width="16" height="8" viewBox="0 0 16 8"><path d="M0 4h13M10 1l4 3-4 3" stroke="#2c8fd6" stroke-width="2" fill="none"/></svg></div>
</div>
<div class="service" style="left:853px;top:1204px">
  <div class="icon"><svg width="50" height="50" viewBox="0 0 50 50" fill="none" stroke="#2c8fd6" stroke-width="2"><rect x="13" y="11" width="24" height="30" rx="1"/><rect x="20" y="8" width="10" height="6"/><path d="M25 20v14M18 27h14"/></svg></div>
  <h3>Lorem ipsum</h3>
  <p>Duis aute irure dolor in reprehenderit in voluptate velit esse cillum dolore eu fugiat nulla pariatur.</p>
  <div class="more">Read More <svg width="16" height="8" viewBox="0 0 16 8"><path d="M0 4h13M10 1l4 3-4 3" stroke="#2c8fd6" stroke-width="2" fill="none"/></svg></div>
</div>

<section class="abs about-band">
  <h2>ABOUT US</h2>
  <div class="divider"><span></span><i></i><span></span></div>
  <p>Lorem ipsum dolor sit amet, consectetur adipiscing elit, sed do eiusmod tempor incididunt ut labore et dolore magna aliqua. Ut enim ad minim veniam, quis nostrud exercitation ullamco laboris nisi ut aliquip ex ea commodo consequat.</p>
  <a class="btn-outline">Read More</a>
</section>
<div class="abs about-photo" role="img" aria-label="Photo of colleagues in a meeting around a conference table"></div>

<h2 class="section-title" style="top:2059px">OUR BENEFITS</h2>
<div class="divider" style="top:2113px"><span></span><i></i><span></span></div>
<p class="lead" style="left:225px;top:2158px;width:750px">Lorem ipsum dolor sit amet, consectetur adipiscing elit, sed do eiusmod tempor incididunt ut labore et dolore magna aliqua Ut enim adi ut aliquip ex ea commodo consequat.</p>

<div class="abs photo-handshake" role="img" aria-label="Photo of a doctor shaking hands with a businessman while medical staff stand behind"></div>
<div class="abs timeline"></div>
<div class="benefit" style="top:2248px"><div class="dot"><b></b></div><h3>Lorem ipsum dolor</h3><p>Duis aute irure dolor in reprehenderit in voluptate velit esse cillum dolore eu fugiat nulla pariatur. Excepteur sint occaecat cupidatat laborum.</p></div>
<div class="benefit" style="top:2352px"><div class="dot"><b></b></div><h3>Lorem ipsum dolor</h3><p>Duis aute irure dolor in reprehenderit in voluptate velit esse cillum dolore eu fugiat nulla pariatur. Excepteur sint occaecat cupidatat laborum.</p></div>
<div class="benefit" style="top:2459px"><div class="dot"><b></b></div><h3>Lorem ipsum dolor</h3><p>Duis aute irure dolor in reprehenderit in voluptate velit esse cillum dolore eu fugiat nulla pariatur. Excepteur sint occaecat cupidatat laborum.</p></div>

<section class="abs testi-band"></section>
<h2 class="section-title" style="top:2701px">CUSTOMER TESTIMONIALS</h2>
<div class="divider" style="top:2760px"><span style="width:100px"></span><i></i><span style="width:100px"></span></div>
<div class="testi" style="left:111px"><div class="avatar" role="img" aria-label="Customer portrait"></div><p>“ Lorem ipsum dolor sit amet, consectetur adipiscing elit, sed do eiusmod tempor incididunt ut labore et dolore magna aliqua. ”</p><div class="who">- Duis aute irure<small>Sit amet.</small></div></div>
<div class="testi" style="left:607px"><div class="avatar" role="img" aria-label="Customer portrait"></div><p>“ Lorem ipsum dolor sit amet, consectetur adipiscing elit, sed do eiusmod tempor incididunt ut labore et dolore magna aliqua. ”</p><div class="who">- Duis aute irure<small>Sit amet.</small></div></div>
<div class="abs dots"><i></i><i></i><i></i><i></i></div>

<footer class="site-footer">
  <div class="brand">VELTRA METRICS</div>
  <p class="f-about">Lorem ipsum dolor sit amet, consectetur adipiscing elit. sed do eiusmod tempor incididunt ut labore et dolore magna aliqua.</p>
  <div class="f-head" style="left:381px">QUICK LINK</div>
  <ul class="f-links"><li>Home</li><li>About Us</li><li>Serives</li><li>Benefits</li><li>Testimonials</li><li>Contact Us</li></ul>
  <div class="f-head" style="left:558px">CONTACT US</div>
  <div class="f-contact">
    <div><svg width="12" height="16" viewBox="0 0 12 16"><path d="M6 0a6 6 0 0 0-6 6c0 4 6 10 6 10s6-6 6-10a6 6 0 0 0-6-6zm0 8.5A2.5 2.5 0 1 1 6 3.5a2.5 2.5 0 0 1 0 5z" fill="#fff"/></svg><span>104 Lorem ipsum dolor<br>sit amet.</span></div>
    <div><svg width="16" height="12" viewBox="0 0 16 12" fill="none" stroke="#fff" stroke-width="1.5"><rect x="1" y="1" width="14" height="10" rx="1"/><path d="M1 1l7 6 7-6"/></svg><span>hello@veltrametrics.example</span></div>
    <div><svg width="14" height="14" viewBox="0 0 14 14"><path d="M3 0l2 3-1.5 1.5a8 8 0 0 0 6 6L11 9l3 2-1.5 2.5C6 13.5.5 8 .5 1.5z" fill="#fff"/></svg><span>(555)-010 2040.</span></div>
  </div>
  <div class="f-head" style="left:827px">NEWSLETTER</div>
  <div class="newsletter"><span>Enter Your Email</span><svg width="13" height="13" viewBox="0 0 14 14" fill="none" stroke="#fff" stroke-width="1.4"><path d="M13 1L1 6l5 2 2 5z"/><path d="M13 1L6 8"/></svg></div>
  <div class="social"><i></i><i></i><i></i><i></i></div>
  <div class="f-rule"></div>
  <p class="copyright">© 2020 Veltra Metrics Pvt Ltd. All rights reserved.</p>
</footer>

</body>
</html>
```